One of a kind service business!

We are the only ocean freight auditing company in the entire world that does what we do. We provide a innovative service in auditing our clients invoices for billing errors as it relates to the import and export of their products anywhere in the world. We'd like to retain the current logo - but we are open to any interesting concepts that can complete the card.

Target Market(s)

C-Level and Senior Financial executives

Industry/Entity Type

Auditing

Requirements
Must have

• ONE SIDED ONLY
Should not have
• no cartoonish images

```html
<!DOCTYPE html>
<html lang="en">
<head>
<meta charset="utf-8">
<title>Tidewell Review – Business Card</title>
<link rel="stylesheet" href="https://fonts.googleapis.com/css2?family=Open+Sans:wght@400;600&display=swap">
<style>
  :root {
    --page-bg: #e6e7e8;
    --card-bg: #ffffff;
    --brand-blue: #0f72ad;
    --brand-green: #11953d;
    --icon-blue: #1d5fa6;
    --ink: #1c1c1c;
    --on-dark: #ffffff;
  }
  * { margin: 0; padding: 0; box-sizing: border-box; }
  html, body {
    width: 1200px;
    height: 944px;
    overflow: hidden;
    background: var(--page-bg);
    font-family: "Open Sans", Verdana, sans-serif;
  }
  .business-card {
    position: absolute;
    left: 100px;
    top: 187px;
    width: 1000px;
    height: 569px;
    background: var(--card-bg);
    border-radius: 36px;
    overflow: hidden;
  }
  .card-waves {
    position: absolute;
    inset: 0;
    width: 1000px;
    height: 569px;
  }
  .brand-name {
    position: absolute;
    left: 50px;
    top: 82px;
    font-size: 58px;
    font-weight: 600;
    line-height: 1;
    color: var(--brand-blue);
    letter-spacing: 0.5px;
  }
  .contact-list {
    position: absolute;
    left: 70px;
    top: 208px;
    list-style: none;
    color: var(--ink);
    font-size: 27px;
    line-height: 35px;
  }
  .contact-item {
    display: flex;
    align-items: flex-start;
  }
  .contact-item.address { margin-bottom: 12px; }
  .contact-icon {
    width: 26px;
    height: 26px;
    margin: 5px 16px 0 0;
    flex: none;
    fill: var(--icon-blue);
  }
  .holder {
    position: absolute;
    right: 0;
    width: 400px;
    text-align: center;
    color: var(--on-dark);
  }
  .holder-name {
    top: 446px;
    font-size: 38px;
    line-height: 1.2;
  }
  .holder-title {
    top: 496px;
    font-size: 26px;
    line-height: 1.2;
  }
</style>
</head>
<body>
  <div class="business-card">
    <svg class="card-waves" viewBox="0 0 1000 569" aria-hidden="true">
      <path fill="var(--brand-green)" d="M600 0 C690 100 690 200 620 300 C560 390 530 480 522 569 L1000 569 L1000 0 Z"/>
      <path fill="var(--brand-blue)" d="M726 0 C745 90 725 200 668 300 C620 385 592 470 586 569 L1000 569 L1000 0 Z"/>
    </svg>

    <div class="brand-name">Tidewell Review</div>

    <ul class="contact-list">
      <li class="contact-item address">
        <svg class="contact-icon" viewBox="0 0 24 24"><path d="M12 3 2 12h3v9h5v-6h4v6h5v-9h3z"/></svg>
        <span>Harbor Point Center<br>Lindenova 12, Prague<br>Czech Republic 11000</span>
      </li>
      <li class="contact-item">
        <svg class="contact-icon" viewBox="0 0 24 24"><path d="M7 2c1 0 2 3 2 5s-2 2-2 3 3 6 5 7c1 0 1-2 3-2s5 1 5 2-2 5-4 5C9 22 2 15 2 8c0-3 3-6 5-6z"/></svg>
        <span>+420 200 555 014</span>
      </li>
      <li class="contact-item">
        <svg class="contact-icon" viewBox="0 0 24 24"><path d="M8 1h8a2 2 0 0 1 2 2v18a2 2 0 0 1-2 2H8a2 2 0 0 1-2-2V3a2 2 0 0 1 2-2zm0 3v13h8V4zm4 15a1.2 1.2 0 1 0 0 2.4 1.2 1.2 0 0 0 0-2.4z"/></svg>
        <span>+420 600 555 027</span>
      </li>
      <li class="contact-item">
        <svg class="contact-icon" viewBox="0 0 24 24"><path d="M7 2c1 0 2 3 2 5s-2 2-2 3 3 6 5 7c1 0 1-2 3-2s5 1 5 2-2 5-4 5C9 22 2 15 2 8c0-3 3-6 5-6z"/></svg>
        <span>+1 555 010 4477 - USA</span>
      </li>
      <li class="contact-item">
        <svg class="contact-icon" viewBox="0 0 24 24"><path d="M7 2h8l3 3v5H7zM4 11h16a2 2 0 0 1 2 2v6h-4v3H6v-3H2v-6a2 2 0 0 1 2-2zm4 6v3h8v-3z"/></svg>
        <span>+420 200 555 090</span>
      </li>
      <li class="contact-item">
        <svg class="contact-icon" viewBox="0 0 24 24"><path d="M12 2a10 10 0 1 0 0 20 10 10 0 0 0 0-20zm6.9 9h-3a15 15 0 0 0-1.4-6 8 8 0 0 1 4.4 6zM12 4.1c1 1.4 1.8 4 1.9 6.9h-3.8c.1-2.9.9-5.5 1.9-6.9zM9.5 5a15 15 0 0 0-1.4 6h-3a8 8 0 0 1 4.4-6zm-4.4 8h3a15 15 0 0 0 1.4 6 8 8 0 0 1-4.4-6zm6.9 6.9c-1-1.4-1.8-4-1.9-6.9h3.8c-.1 2.9-.9 5.5-1.9 6.9zm2.5-.9a15 15 0 0 0 1.4-6h3a8 8 0 0 1-4.4 6z"/></svg>
        <span>www.tidewellreview.net</span>
      </li>
      <li class="contact-item">
        <svg class="contact-icon" viewBox="0 0 24 24"><path d="M2 9 12 3l10 6v12H2zm2 2.5V19h16v-7.5l-8 5z"/></svg>
        <span>danielm@tidewellreview.net</span>
      </li>
    </ul>

    <div class="holder holder-name">Daniel Marsh</div>
    <div class="holder holder-title">CEO</div>
  </div>
</body>
</html>
```